MUSIC FESTIVAL 2023

On the occasion of the 2023 music festival, the 24th, brings the VELMORANTE group to its terrace.
We are organizing a giant barbecue on this occasion.
This event is organized in collaboration with LE BRUMAIRE.
Possibility of take-out!
Address of the event: 12-16 Rue Fernand Lavigne in CAMBRAI.4
From 19h.
03 41 58 62 19 - marc@orvaline-habitat.example
Please write in French.
To use the logos of the two establishments.

```html
<!DOCTYPE html>
<html lang="fr">
<head>
<meta charset="utf-8">
<title>Fête de la Musique 2023 — Le Sextant</title>
<link rel="stylesheet" href="https://fonts.googleapis.com/css2?family=Anton&family=Montserrat:wght@400;700;800;900&family=Poppins:wght@400;500;700&display=swap">
<style>
  :root {
    --bg-page: #ffffff;
    --plum-deep: #3c0426;
    --plum: #5e0a3d;
    --plum-light: #7d1454;
    --pink: #ec2a86;
    --white: #ffffff;
    --wood: #c9761f;
    --wood-dark: #7a3e0c;
  }
  * { box-sizing: border-box; margin: 0; padding: 0; }
  html, body { width: 1200px; height: 2432px; overflow: hidden; background: var(--bg-page); }
  .flyer {
    position: absolute; left: 100px; top: 566px; width: 1000px; height: 1300px; overflow: hidden;
    background: radial-gradient(ellipse at 70% 35%, var(--plum-light) 0%, var(--plum) 40%, var(--plum-deep) 100%);
    box-shadow: 0 10px 30px rgba(0,0,0,.35);
    font-family: 'Poppins', sans-serif; color: var(--white);
  }
  .guitar-photo {
    position: absolute; right: 0; top: 0; width: 380px; height: 1300px;
    background: linear-gradient(180deg, #3a2418 0%, #2a1a12 45%, var(--wood) 62%, var(--wood-dark) 100%);
    clip-path: polygon(40% 0, 100% 0, 100% 100%, 0 100%, 0 72%, 30% 62%, 40% 55%);
  }
  .brand-mark { position: absolute; left: 540px; top: 60px; width: 230px; height: 210px; display: flex; align-items: center; gap: 12px; }
  .brand-mark .dot { width: 22px; height: 22px; border-radius: 50%; background: var(--white); flex: none; }
  .brand-mark .name { font-family: 'Montserrat', sans-serif; font-weight: 700; font-size: 34px; color: var(--white); }
  .occasion { position: absolute; left: 40px; top: 36px; font-size: 40px; font-weight: 400; }
  .year { position: absolute; left: 36px; top: 88px; font-family: 'Montserrat', sans-serif; font-weight: 900; font-size: 118px; line-height: 1; color: var(--pink); }
  .title-top { position: absolute; left: 40px; top: 218px; font-family: 'Anton', sans-serif; font-size: 118px; line-height: 1; }
  .title-main { position: absolute; left: 38px; top: 352px; font-family: 'Montserrat', sans-serif; font-weight: 900; font-size: 112px; line-height: 1; letter-spacing: -1px; }
  .intro { position: absolute; left: 40px; top: 470px; font-size: 44px; color: var(--pink); }
  .intro b { font-family: 'Montserrat', sans-serif; font-weight: 800; color: var(--white); }
  .band-name { position: absolute; left: 40px; top: 530px; font-family: 'Anton', sans-serif; font-size: 104px; line-height: 1; letter-spacing: 2px; }
  .terrace { position: absolute; left: 42px; top: 646px; font-size: 50px; color: var(--pink); }
  .rule { position: absolute; left: 42px; width: 480px; height: 2px; background: linear-gradient(90deg, var(--pink), rgba(236,42,134,.3)); }
  .date-block { position: absolute; left: 38px; top: 736px; display: flex; align-items: center; font-family: 'Montserrat', sans-serif; font-weight: 800; }
  .date-year { writing-mode: vertical-rl; transform: rotate(180deg); color: var(--pink); font-size: 38px; line-height: 1; margin-right: 10px; }
  .date-day { font-size: 48px; line-height: 1.15; }
  .date-sep { width: 3px; height: 96px; background: var(--pink); margin: 0 24px 0 28px; }
  .date-time { font-size: 48px; line-height: 1.15; }
  .date-time .label { color: var(--pink); }
  .address { position: absolute; left: 40px; top: 862px; display: flex; gap: 14px; font-size: 27px; line-height: 1.2; }
  .feature { position: absolute; left: 42px; top: 960px; display: flex; align-items: center; }
  .feature .bbq { font-size: 27px; color: var(--pink); line-height: 1.3; }
  .feature .bbq strong { display: block; font-family: 'Anton', sans-serif; font-weight: 400; font-size: 32px; color: var(--white); }
  .feature .sep { width: 3px; height: 116px; background: var(--white); margin: 0 24px; }
  .partner .label { font-size: 21px; color: var(--pink); }
  .partner .name { font-family: 'Montserrat', sans-serif; font-weight: 700; font-size: 40px; margin-top: 8px; }
  .phone { position: absolute; left: 40px; top: 1108px; display: flex; align-items: center; gap: 16px; font-family: 'Montserrat', sans-serif; font-weight: 800; font-size: 58px; }
  .footer-band { position: absolute; left: 0; bottom: 0; width: 1000px; height: 110px; }
  .email { position: absolute; left: 40px; top: 1212px; display: flex; align-items: center; gap: 14px; font-size: 27px; }
</style>
</head>
<body>
<main class="flyer">
  <div class="guitar-photo" role="img" aria-label="Photographie d'une guitare classique en bois"></div>

  <div class="brand-mark"><span class="dot"></span><span class="name">Le Sextant</span></div>

  <p class="occasion">À l'occasion de</p>
  <p class="year">2023</p>
  <h1 class="title-top">FÊTE DE LA</h1>
  <p class="title-main">MUSIQUE</p>
  <p class="intro"><b>LE SEXTANT</b> apporte le groupe</p>
  <p class="band-name">VELMORANTE</p>
  <p class="terrace">à sa terrasse.</p>

  <div class="rule" style="top:722px"></div>

  <div class="date-block">
    <span class="date-year">2023</span>
    <div class="date-day">THURSDAY<br>15TH JUNE</div>
    <span class="date-sep"></span>
    <div class="date-time"><span class="label">STARTS</span><br>6.30 PM</div>
  </div>

  <div class="address">
    <svg width="22" height="30" viewBox="0 0 22 30"><path d="M11 1C5.5 1 1.5 5 1.5 10.3 1.5 17 11 28 11 28s9.5-11 9.5-17.7C20.5 5 16.5 1 11 1z" fill="none" stroke="#fff" stroke-width="2.5"/><circle cx="11" cy="10.5" r="3.5" fill="#fff"/></svg>
    <p>12-16 Rue Fernand Lavigne in CAMBRAI.4<br>From 19h.</p>
  </div>

  <div class="rule" style="top:938px"></div>

  <div class="feature">
    <p class="bbq">Nous organisons<strong>UN BARBECUE GÉANT</strong>à cette occasion.</p>
    <span class="sep"></span>
    <div class="partner">
      <p class="label">En collaboration avec</p>
      <p class="name">Le Brumaire</p>
    </div>
  </div>

  <div class="phone">
    <svg width="48" height="48" viewBox="0 0 48 48" fill="none" stroke="#fff" stroke-width="2.5" stroke-linejoin="round"><path d="M10 6l8 9-4 5c2 5 7 10 12 12l5-4 9 8-4 6C22 42 6 26 4 12z"/><path d="M28 6a14 14 0 0 1 14 14M28 13a7 7 0 0 1 7 7"/></svg>
    <span>03 41 58 62 19</span>
  </div>

  <svg class="footer-band" viewBox="0 0 1000 110" preserveAspectRatio="none">
    <path d="M0 20 C300 -5 650 20 1000 70 L1000 110 L0 110 Z" fill="#3a0323"/>
    <path d="M0 20 C300 -5 650 20 1000 70" fill="none" stroke="#ec2a86" stroke-width="3"/>
  </svg>

  <div class="email">
    <svg width="26" height="24" viewBox="0 0 26 24" fill="none" stroke="#fff" stroke-width="2"><rect x="2" y="6" width="22" height="16" rx="1"/><path d="M2 7l11 8 11-8"/></svg>
    <span>marc@orvaline-habitat.example</span>
  </div>
</main>
</body>
</html>
```